New "Farol Sereno" (The Quiet Lantern) wordpress layout

What we look for: Wordpress Theme ready to be installed in the Wordpress, even if it requires some plugins to work.

[Introduction]
Farol Sereno (www.FarolSereno.com.br) is a non-profit Secular Humanist blog in Brazil, with hundreds of thousands of visits per month and new posts almost every day. Maintained exclusivelly by volunteers, the blog has more or less the same layout since the foundation in 2009, and we believe it is time to change. We want "Farol" to become lighter, simpler and more responsive to new browsers and screen widths.

[General Concept]
The blog is about Secular Humanism (http://en.openlexa-ref.org/page/Secular_humanism) and covers humanism, secularism, sciences in general, LGBT rights, feminism, human rights, amongst other topics.

In Portuguese, "Farol Sereno" means a "Quiet Lantern", a direct reference to Edmund Hartley's teapot analogy (http://en.openlexa-ref.org/page/Hartley_lantern) so, at the top of the theme, we really wanted to have a Quiet Lantern somewhere, maybe a Quiet Lantern through the space amongst planets (it could be Earth itself) or just the teapot at space. This image here (http://img.orbitvista-demo.net/pics/48812/full/Kelvora.jpg?1298450117) illustrates the concept, with space at the background and a transparent asteroid at the forefront.

We want a clean, elegant and contemporary design with white background for posts and fonts for reading long (mostly 1-3 page) texts.

We also want an image-based slider such as GlideRoll that would promote the latest posts.

[Technical requirements]
* Fully responsive design
* SEO -friendly, with page titles with h1 tags, breadcrumbs, pagination, next and previous post/page links, related posts, clean semantics
* Cross-browser compatibility (minimum Chrome, IE, Firefox and Safari)
* NO ads slots (site is a non-profit and we DO NOT want any advertisement)
* Widget-ready (at the right side)
* Google analytics friendly
* Social media icons (You Tube, Socialnet, Twitter)
* Georgia font for the post's body
* Helvetica bold font for the title
* At the bottom of each post, a small disclaimer (text to be defined) with dotted square
* White background for posts (#FFFFFF)

Target Market(s)

Secular Humanists in Brazil

Industry/Entity Type

Non-Profit

Requirements
Must have
• * A nice Quiet Lantern image at the top
* White background for posts
* Must work well with long texts
* SEO-friendly
* Fully responsible design
Nice to have
• * JQuery enhancements
* Featured (high-def) image at the top of each post
* GlideRoll at the homepage, looping through featured images of the latest posts (e.g., the latest 5)
- Group posts by categories in the homepage. Such as a magazine style, where we will have "sections", with thumbnails and the titles. Latest posts should also be listed below these grouped posts.
- A grid of related texts at the end of each post, with 5-8 sugestions, half matched by keywords/title proximity and half by a category of choice.
Should not have
• * Advertisement area

```html
<!DOCTYPE html>
<html lang="en">
<head>
<meta charset="utf-8">
<title>Farol Sereno — Blog</title>
<link href="https://fonts.googleapis.com/css2?family=Arimo:wght@400;700&family=Gelasio:wght@400;700&display=swap" rel="stylesheet">
<style>
:root{
  --space-mid:#3a1422;
  --maroon:#2a0a12;
  --cream:#f6efe4;
  --frame:#fbf8f5;
  --paper:#ffffff;
  --beige:#e9ddcc;
  --beige-dark:#cdb89c;
  --brown:#5a3228;
  --brown-dark:#3b1d16;
  --ink:#3a2a22;
  --text:#4b3d36;
  --muted:#7a6a60;
  --line:#ddd2c6;
  --date-bg:#efe8e0;
  --social-blue:#3b5b9a;
  --social-sky:#1f7bbf;
  --social-orange:#e8801e;
  --social-red:#c6322a;
}
*{box-sizing:border-box;margin:0;padding:0}
html,body{width:1200px;height:2356px;overflow:hidden}
body{position:relative;background:linear-gradient(180deg,var(--space-mid) 0,#2e0d18 600px,var(--maroon) 1100px,#220810 2356px);font-family:"Gelasio",Georgia,serif;color:var(--text)}
.space-backdrop{position:absolute;left:0;top:0;width:1200px;height:1100px;background:radial-gradient(ellipse at 55% 10%,#5b2a3c 0,transparent 45%),radial-gradient(ellipse at 95% 40%,#4a2030 0,transparent 40%)}
.planet-art{position:absolute;left:900px;top:-40px;width:520px;height:560px;border-radius:50%;background:radial-gradient(circle at 30% 40%,#9a6a72 0,#5a2e3c 45%,#2c0e18 75%);opacity:.55}
.planet-small{position:absolute;left:1160px;top:150px;width:90px;height:140px;border-radius:50%;background:radial-gradient(circle at 30% 40%,#c89a86,#6a3a32);opacity:.8}
.teapot-art{position:absolute;left:505px;top:0;width:180px;height:160px;border-radius:10px;background:radial-gradient(ellipse at 50% 50%,#d9cfc8 0,#8a7278 55%,transparent 75%)}
.brand{position:absolute;left:57px;top:46px}
.brand-name{font-family:"Gelasio",Georgia,serif;font-weight:700;font-size:54px;line-height:1;color:var(--cream);letter-spacing:1px}
.brand-tagline{margin-top:8px;font-size:13px;font-weight:700;color:var(--cream)}
.search{position:absolute;left:880px;top:103px;width:268px;height:28px;background:var(--cream);border-radius:4px;display:flex;align-items:center;justify-content:space-between;padding:0 10px;font-size:12px;color:var(--muted)}
.page-frame{position:absolute;left:36px;top:155px;width:1127px;height:2142px;background:var(--frame);border-radius:10px;box-shadow:0 0 0 2px #d8cdc2}
.main-nav{display:flex;height:52px;background:linear-gradient(180deg,#f1e8dc,var(--beige-dark));border-radius:10px 10px 0 0;border-bottom:1px solid #b59e82}
.main-nav a{flex:auto;display:flex;align-items:center;justify-content:center;font-size:13px;font-weight:700;letter-spacing:.5px;color:var(--brown-dark);text-decoration:none;border-right:1px solid #b9a388}
.main-nav a:last-child{border-right:0}
.slider{position:absolute;left:20px;top:70px;width:1077px;height:366px;background:var(--paper);border:1px solid var(--line);border-radius:6px;padding:6px}
.slide-photo{position:absolute;left:6px;top:6px;width:766px;height:352px;background:linear-gradient(135deg,#6b4a3a,#a88c78 40%,#c8c2c8 70%,#5a4a46)}
.slide-panel{position:absolute;left:772px;top:6px;width:298px;height:352px;background:var(--beige);border:4px solid #d6c3aa;padding:20px 22px}
.slide-title{font-family:"Arimo",Helvetica,sans-serif;font-weight:700;font-size:25px;color:var(--ink)}
.slide-date{font-size:14px;font-weight:700;color:var(--ink);margin:6px 0 14px}
.slide-text{font-size:13.5px;line-height:25px;color:var(--text)}
.btn-more{display:inline-block;margin-top:20px;background:var(--brown-dark);color:var(--cream);font-size:12px;font-weight:700;letter-spacing:1px;padding:8px 14px;border-radius:4px}
.slide-dots{display:flex;gap:5px;margin-top:18px}
.slide-dots span{width:9px;height:9px;border-radius:50%;background:#9a8a80}
.slide-dots span:first-child{background:var(--brown-dark)}
.content{position:absolute;left:21px;top:465px;width:777px;height:1655px;background:var(--paper);border:1px solid var(--line);border-radius:6px}
.post{position:absolute;left:20px;width:737px}
.post-head{display:flex;gap:18px;align-items:flex-start}
.post-date{width:80px;height:74px;background:var(--date-bg);display:flex;flex-direction:column;align-items:center;justify-content:center;font-family:"Arimo",Helvetica,sans-serif;font-size:23px;line-height:1.15;color:var(--ink)}
.post-title{font-family:"Arimo",Helvetica,sans-serif;font-weight:700;font-size:24px;line-height:1.15;color:var(--ink);margin-top:4px}
.post-author{font-family:"Arimo",Helvetica,sans-serif;font-weight:700;font-size:12.5px;color:var(--ink);margin-top:6px}
.post-body{margin-top:10px;font-size:14px;line-height:25px;color:var(--text);text-align:justify}
.post-body p{margin-bottom:10px}
.post-thumb{float:left;width:340px;height:236px;margin:0 20px 6px 0}
.thumb-group{background:linear-gradient(135deg,#e8d2c8,#c9a89a 50%,#7e8fa6)}
.thumb-audience{background:linear-gradient(135deg,#c9b8a0,#7a6050 50%,#3a2e2a)}
.thumb-video{background:linear-gradient(135deg,#f2eee9,#d8cfc6 50%,#b84a3a)}
.share{clear:both;display:flex;align-items:center;gap:5px;font-size:12.5px;color:var(--ink);padding:8px 0 14px;border-bottom:2px dotted #9a8a80}
.share span{margin-right:4px}
.share i{width:18px;height:18px;border-radius:2px;display:inline-block}
.sidebar{position:absolute;left:810px;top:465px;width:297px}
.widget{margin-bottom:22px}
.widget-title{height:46px;background:linear-gradient(180deg,var(--brown),var(--brown-dark));border-radius:6px 6px 0 0;color:#fff;font-family:"Arimo",Helvetica,sans-serif;font-weight:700;font-size:19px;display:flex;align-items:center;padding-left:20px}
.widget-body{padding:12px 14px 8px 18px}
.widget-list{list-style:none}
.widget-list li{position:relative;padding-left:18px;font-size:13px;line-height:20px;color:var(--text);margin-bottom:11px}
.widget-list li::before{content:"";position:absolute;left:2px;top:7px;border:4px solid transparent;border-left:5px solid #9a8a80}
.select{height:36px;background:#fff;border:1px solid #cfc4ba;border-radius:5px;display:flex;align-items:center;justify-content:space-between;padding-left:16px;font-size:12.5px;color:var(--muted)}
.select b{width:28px;height:100%;border-left:1px solid #cfc4ba;display:flex;align-items:center;justify-content:center}
.social-box{background:#fff;border:1px solid var(--line);padding:12px;font-family:"Arimo",Helvetica,sans-serif;font-size:11px;color:#444}
.social-row{display:flex;gap:10px}
.social-avatar{width:54px;height:54px;border:1px solid #ccc;display:flex;align-items:center;justify-content:center}
.social-avatar span{width:30px;height:30px;border-radius:50%;background:var(--brown-dark)}
.like-btn{display:inline-block;margin:6px 0;border:1px solid #9aa8c8;background:#eef1f8;padding:2px 6px;font-size:11px;color:#3b4a6a}
.social-foot{display:flex;align-items:center;justify-content:space-between;margin-top:12px;padding-right:60px}
.login-btn{background:var(--social-blue);color:#fff;font-weight:700;padding:3px 9px;font-size:11px}
.footer{position:absolute;left:0;top:2308px;width:1200px;text-align:center;font-size:12px;color:var(--cream)}
.footer-social{position:absolute;left:1036px;top:2305px;display:flex;gap:5px}
.footer-social i{width:19px;height:19px;border-radius:2px}
.c-blue{background:var(--social-blue)}.c-sky{background:var(--social-sky)}.c-orange{background:var(--social-orange)}.c-red{background:var(--social-red)}
</style>
</head>
<body>
<div class="space-backdrop"></div>
<div class="planet-art" role="img" aria-label="Large planet glowing in deep space"></div>
<div class="planet-small" role="img" aria-label="Small distant planet"></div>
<div class="teapot-art" role="img" aria-label="Flying lantern illustration among the stars"></div>

<header class="brand">
  <h1 class="brand-name">Farol Sereno</h1>
  <p class="brand-tagline">Blog oficial da liga serena de pensamento livre. Criado em 04/03/2010</p>
</header>
<div class="search">Search here..
  <svg width="14" height="14" viewBox="0 0 14 14"><circle cx="6" cy="6" r="4.5" fill="none" stroke="#3b1d16" stroke-width="1.8"/><line x1="9.3" y1="9.3" x2="13" y2="13" stroke="#3b1d16" stroke-width="2"/></svg>
</div>

<div class="page-frame">
  <nav class="main-nav">
    <a href="#">INITIATION</a><a href="#">FAROLCAST</a><a href="#">CONTACT US</a><a href="#">ABOUT</a><a href="#">JOURNAL LANTERN</a><a href="#">FRIENDS</a><a href="#">PANEL OF THE LANTERN</a><a href="#">EDITORIAL LINE</a>
  </nav>

  <section class="slider">
    <div class="slide-photo" role="img" aria-label="Conference hall with audience seated at round tables"></div>
    <div class="slide-panel">
      <h2 class="slide-title">Latest Posts Tittle</h2>
      <p class="slide-date">Posted on 09 Dec 2012</p>
      <p class="slide-text">Mauris vel lacus vitae felis vestibulum volutpat. Etiam est nunc, venenatis in, tristique eu, imperdiet ac, nisl. Cum sociis natoque penatibus et magnis dis parturient montes, nascetur ridiculus mus. In iaculis facilisis massa.</p>
      <span class="btn-more">LEARN MORE</span>
      <div class="slide-dots"><span></span><span></span><span></span><span></span><span></span></div>
    </div>
  </section>

  <main class="content">
    <article class="post" style="top:18px">
      <div class="post-head">
        <div class="post-date">05<br>Dec</div>
        <div><h2 class="post-title">Response to Helena Vasconde attack against<br>the secular state</h2><p class="post-author">Author : Livia Moranti</p></div>
      </div>
      <div class="post-body">
        <div class="post-thumb thumb-group" role="img" aria-label="Group of colleagues standing together"></div>
        <p>Lorem ipsum dolor sit amet, consectetuer adipiscing elit. Nam cursus. Morbi ut mi. Nullam enim leo, egestas id, condimentum at, laoreet mattis, massa.</p>
        <p>Sed eleifend nonummy diam. Praesent mauris ante, elementum et, bibendum at, posuere sit amet, nibh. Duis tincidunt lectus quis dui viverra vestibulum. Suspendisse vulputate aliquam dui. Nulla elementum dui ut augue. Aliquam vehicula mi at mauris. Maecenas placerat, nisl at consequat rhoncus, sem nunc gravida justo, quis eleifend arcu velit quis lacus. Etiam est nunc, venenatis in, tristique eu, imperdiet ac, nisl. Cum sociis natoque penatibus et magnis dis parturient montes, nascetur ridiculus mus. In iaculis facilisis massa. Etiam eu urna. Sed porta. Suspendisse quam leo, molestie sed, luctus quis, feugiat in, pede. Fusce tellus. Sed metus augue, convallis et, vehicula ut.</p>
      </div>
      <div class="share"><span>Share this Blog Post</span><i class="c-blue"></i><i class="c-sky"></i><i class="c-orange"></i><i class="c-red"></i></div>
    </article>

    <article class="post" style="top:505px">
      <div class="post-head">
        <div class="post-date">04<br>Dec</div>
        <div><h2 class="post-title">Respond these feminists! Part II</h2><p class="post-author">Author : Livia Moranti</p></div>
      </div>
      <div class="post-body">
        <div class="post-thumb thumb-audience" style="height:198px" role="img" aria-label="Audience listening to a speaker in a lecture room"></div>
        <p>Lorem ipsum dolor sit amet, consectetuer adipiscing elit. Nam cursus. Morbi ut mi. Nullam enim leo, egestas id, condimentum at, laoreet mattis, massa.</p>
        <p>Sed eleifend nonummy diam. Praesent mauris ante, elementum et, bibendum at, posuere sit amet, nibh. Duis tincidunt lectus quis dui viverra vestibulum. Suspendisse vulputate aliquam dui. Nulla elementum dui ut augue. Aliquam vehicula mi at mauris. Nunc tempus felis vitae urna. Vivamus porttitor, neque at volutpat rutrum, purus nisi eleifend libero, a tempus libero lectus feugiat felis. Morbi diam mauris, viverra in, gravida eu, mattis in, ante. Morbi eget arcu. Morbi porta, libero id ullamcorper nonummy, nibh ligula pulvinar metus, eget consectetuer augue nisi quis lacus. Ut ac mi quis lacus mollis aliquam. Curabitur iaculis tempus eros.</p>
      </div>
      <div class="share"><span>Share this Blog Post</span><i class="c-blue"></i><i class="c-sky"></i><i class="c-orange"></i><i class="c-red"></i></div>
    </article>

    <article class="post" style="top:992px">
      <div class="post-head">
        <div class="post-date">02<br>Dec</div>
        <div><h2 class="post-title">Mentelivre.VLOG.br: Dorian Whitcombe and<br>the denial of racism</h2><p class="post-author">Author : Livia Moranti</p></div>
      </div>
      <div class="post-body">
        <div class="post-thumb thumb-video" style="height:198px" role="img" aria-label="Desk with notes, glasses, tablet and a rising chart"></div>
        <p>Lorem ipsum dolor sit amet, consectetuer adipiscing elit. Nam cursus. Morbi ut mi. Nullam enim leo, egestas id, condimentum at, laoreet mattis, massa.</p>
        <p>Sed eleifend nonummy diam. Praesent mauris ante, elementum et, bibendum at, posuere sit amet, nibh. Duis tincidunt lectus quis dui viverra vestibulum. Suspendisse vulputate aliquam dui. Nulla elementum dui ut augue. Aliquam vehicula mi at mauris. Nunc tempus felis vitae urna. Vivamus porttitor, neque at volutpat rutrum, purus nisi eleifend libero, a tempus libero lectus feugiat felis. Morbi diam mauris, viverra in, gravida eu, mattis in, ante. Morbi eget arcu. Morbi porta, libero id ullamcorper nonummy, nibh ligula pulvinar metus, eget consectetuer augue nisi quis lacus. Ut ac mi quis lacus mollis aliquam. Curabitur iaculis tempus eros.</p>
        <p>Lorem ipsum dolor sit amet, consectetuer adipiscing elit. Nam cursus. Morbi ut mi. Nullam enim leo, egestas id, condimentum at, laoreet mattis, massa. Sed eleifend nonummy diam. Praesent mauris ante, elementum et, bibendum at, posuere sit amet, nibh n iaculis facilisis massa. Etiam eu urna. Sed porta. Suspendisse quam leo, molestie sed, luctus quis, feugiat in, pede. Fusce tellus. Sed metus augue, convallis et, vehicula ut, pulvinar eu, ante. Integer orci tellus, tristique vitae, consequat nec, porta vel, lectus.</p>
      </div>
      <div class="share" style="border-bottom:0"><span>Share this Blog Post</span><i class="c-blue"></i><i class="c-sky"></i><i class="c-orange"></i><i class="c-red"></i></div>
    </article>
  </main>

  <aside class="sidebar">
    <section class="widget">
      <h3 class="widget-title">Recent Posts</h3>
      <ul class="widget-list widget-body">
        <li>Mentelivre.VLOG.br: Dorian Whitcombe and the denial of racism</li>
        <li>Talking (alone / a) is easy</li>
        <li>Response to Helena Vasconde attack against the secular state</li>
        <li>Documentary: The Laughter of Others (Caio Berlinde, 2012)</li>
        <li>Mentelivre.VLOG.br answers vlogger who criticized feminism</li>
      </ul>
    </section>
    <section class="widget">
      <h3 class="widget-title">Recent Comments</h3>
      <ul class="widget-list widget-body">
        <li>LucasFerreiraDaMota on Talking (alone / a) is easy</li>
        <li>Rafael Quintino on Respond these feminists! Part II</li>
        <li>Bruno Teixal on Respond these feminists! Part II</li>
        <li>Otavio Lemare on Contest: new design for the Quiet Lantern</li>
        <li>Marcos Alvim Neto on Talking</li>
      </ul>
    </section>
    <section class="widget">
      <h3 class="widget-title">Select Category</h3>
      <div class="widget-body"><div class="select">Category goes here<b><svg width="9" height="6" viewBox="0 0 9 6"><path d="M0 0h9L4.5 6z" fill="#3b1d16"/></svg></b></div></div>
    </section>
    <section class="widget">
      <h3 class="widget-title">Like Us on Socialnet</h3>
      <div class="widget-body">
        <div class="social-box">
          <div class="social-row">
            <div class="social-avatar"><span></span></div>
            <div><strong style="font-size:12px">Farol Sereno</strong><br><span class="like-btn">Like</span><br>5,738 people like Farol Sereno.</div>
          </div>
          <div class="social-foot"><span>Socialnet social plugin</span><span class="login-btn">Log In</span></div>
        </div>
      </div>
    </section>
    <section class="widget">
      <h3 class="widget-title">Notes Links</h3>
      <ul class="widget-list widget-body">
        <li>The Hearing on the "Gay Cure" (sic)</li>
        <li>LSPL endorses GLOBACARE document in favor of the criminalization of homophobia in Brazil</li>
        <li>The Strategy Book: a rebuttal</li>
        <li>Council of Women's Affairs of the Council is now LSPL Feminist</li>
        <li>Dr. Renata Solvane under attack</li>
        <li>Federal Government presents official figures on homophobic murders in 2011</li>
        <li>To whom do you belong?</li>
        <li>LSPL creates Ethics Council Inter-Species</li>
        <li>Why June is Gay Pride Month? Where does all this? And where it goes?</li>
        <li>The world is a garden of delights, but is not Dantesque inferno</li>
      </ul>
    </section>
    <section class="widget">
      <h3 class="widget-title">File</h3>
      <div class="widget-body"><div class="select">Select Month<b><svg width="9" height="6" viewBox="0 0 9 6"><path d="M0 0h9L4.5 6z" fill="#3b1d16"/></svg></b></div></div>
    </section>
  </aside>
</div>

<footer class="footer">Copyright © 2012 Company Name.  All right reserved</footer>
<div class="footer-social"><i class="c-blue"></i><i class="c-sky"></i><i class="c-orange"></i><i class="c-red"></i></div>
</body>
</html>
```